Design a building access mobile app for Quillo by Tamberlin Entry Systems

Hello, We're looking for an awesome designer to create an app design for our app Quillo, by Tamberlin Entry Systems. the mobile app allows employees open their office doors with their mobile phone. this means they don't have to use those plastic card badges or keys. We like clean modern design, dark and light themes. We don't have a logo yet.
Updates

Reason: Waiting on a couple designers to submit concepts

Target Market(s)

Commercial and employees

Industry/Entity Type

Building

Font styles to use
Sans Serif
Other font styles liked:
• Oswald extra light

Requirements
Must have
• nice clean design

```html
<!DOCTYPE html>
<html lang="en">
<head>
<meta charset="utf-8">
<title>Quillo – Onboarding</title>
<link rel="stylesheet" href="https://fonts.googleapis.com/css2?family=Oswald:wght@200;300;400;500&family=Roboto:wght@400;500&display=swap">
<style>
  :root {
    --bg-top: #1f8fd0;
    --bg-bottom: #1b7ec4;
    --screen: #ffffff;
    --ink: #1c1c1c;
    --muted: #3a3a3a;
    --accent: #3a80c9;
    --accent-soft: #8fb7e3;
    --lock-blue: #2a86d1;
    --lock-light: #6fb3e8;
  }
  * { box-sizing: border-box; margin: 0; padding: 0; }
  html, body {
    width: 1200px; height: 864px; overflow: hidden;
  }
  body {
    background: linear-gradient(160deg, var(--bg-top), var(--bg-bottom));
    display: flex; align-items: center; justify-content: center;
    font-family: "Oswald", sans-serif;
  }
  .screen {
    position: relative;
    width: 420px; height: 746px;
    background: var(--screen);
    box-shadow: 0 24px 50px rgba(10, 50, 90, 0.35);
    color: var(--ink);
  }
  .status-bar {
    display: flex; align-items: center; justify-content: space-between;
    height: 22px; padding: 0 8px;
    font-family: "Roboto", sans-serif; font-size: 12px; font-weight: 500;
  }
  .status-left, .status-right { display: flex; align-items: center; gap: 5px; width: 120px; }
  .status-right { justify-content: flex-end; }
  .signal { display: flex; gap: 2px; }
  .signal span { width: 6px; height: 6px; border-radius: 50%; background: var(--ink); }
  .signal span.off { background: none; border: 1px solid var(--ink); }
  .battery { width: 24px; height: 11px; border: 1px solid var(--ink); border-radius: 2px; padding: 1px; position: relative; }
  .battery::after { content: ""; position: absolute; right: -3px; top: 3px; width: 2px; height: 4px; background: var(--ink); }
  .battery i { display: block; height: 100%; width: 77%; background: var(--ink); }
  .hero {
    display: block; width: 180px; height: 150px;
    margin: 70px auto 0;
  }
  .onboard-title {
    margin-top: 72px;
    text-align: center;
    font-size: 28px; font-weight: 400; letter-spacing: 1px;
  }
  .onboard-copy {
    margin: 10px auto 0; width: 320px;
    text-align: center;
    font-size: 13.5px; font-weight: 300; line-height: 1.4; color: var(--muted);
  }
  .pager {
    display: flex; justify-content: center; align-items: center; gap: 10px;
    margin-top: 44px;
  }
  .pager span { width: 10px; height: 10px; border-radius: 50%; background: var(--accent-soft); }
  .pager span.active { width: 16px; height: 16px; background: var(--accent); border: 3px solid #cfe1f5; }
  .btn-next {
    display: block; margin: 60px auto 0;
    width: 350px; height: 58px; border: 0; border-radius: 29px;
    background: var(--accent); color: #dbe8f6;
    font-family: "Oswald", sans-serif; font-size: 17px; font-weight: 300; letter-spacing: 1px;
  }
  .btn-skip {
    display: block; margin: 26px auto 0;
    background: none; border: 0;
    font-family: "Oswald", sans-serif; font-size: 17px; font-weight: 400; letter-spacing: 1px; color: var(--ink);
  }
</style>
</head>
<body>
  <main class="screen">
    <header class="status-bar">
      <div class="status-left">
        <div class="signal"><span></span><span></span><span></span><span class="off"></span><span class="off"></span></div>
        <span class="carrier">Carrio</span>
        <svg width="13" height="10" viewBox="0 0 13 10" aria-hidden="true"><path d="M1 3.5a8 8 0 0 1 11 0M3 5.6a5 5 0 0 1 7 0M5 7.7a2 2 0 0 1 3 0" stroke="#1c1c1c" stroke-width="1.5" fill="none" stroke-linecap="round"/></svg>
      </div>
      <span class="clock">1:23 AM</span>
      <div class="status-right">
        <span>77%</span>
        <div class="battery"><i></i></div>
      </div>
    </header>

    <svg class="hero" viewBox="0 0 180 150" role="img" aria-label="Illustration of an open blue padlock">
      <rect x="20" y="20" width="140" height="120" rx="16" fill="var(--lock-light)" opacity="0.35"/>
      <rect x="50" y="60" width="80" height="64" rx="10" fill="var(--lock-blue)"/>
    </svg>

    <h1 class="onboard-title">SIMPLE, EASY &amp; TIME SAVING</h1>
    <p class="onboard-copy">Lorem ipsum dolor sit amet, consectur adipicing it, sed do eiusmod tempor incididunt ut labore et dolore magna aliqua. Ut enim ad minim veniam, quis nostrud.</p>

    <div class="pager" aria-label="Step 2 of 3"><span></span><span class="active"></span><span></span></div>

    <button class="btn-next">NEXT</button>
    <button class="btn-skip">SKIP</button>
  </main>
</body>
</html>
```